Hacienda Monte Verda Business cards

We would like 3 individual business cards with the logo you designed:

1) Marta Pellingford - Phone: 206 555 0147
2) Theodore R Pellingford - Phone 206 555 0183
3) Dana Moreth - Phone 310-555-0162

Address for all three cards:
7218 142nd Ave NE
Bramwell, WA 98077
HaciendaMonteVerda@brindlemail.com

```html
<!DOCTYPE html>
<html lang="en">
<head>
<meta charset="utf-8">
<title>Hacienda Monte Verda – Business Card</title>
<link rel="stylesheet" href="https://fonts.googleapis.com/css2?family=Cinzel:wght@400&family=Open+Sans:wght@400&display=swap">
<style>
  :root {
    --page: #e9e8e6;
    --card: #f8f8f8;
    --ink: #1a1a1a;
    --ink-soft: #2b2b2b;
    --scene-mid: #dcdcdc;
  }
  * { margin: 0; padding: 0; box-sizing: border-box; }
  html, body {
    width: 1200px;
    height: 997px;
    overflow: hidden;
    background: var(--page);
  }
  .canvas {
    position: relative;
    width: 1200px;
    height: 997px;
  }
  .card {
    position: absolute;
    left: 150px;
    top: 241px;
    width: 900px;
    height: 514px;
    background: var(--card);
    box-shadow: 0 6px 24px rgba(0,0,0,0.10), 0 1px 3px rgba(0,0,0,0.08);
    overflow: hidden;
  }
  .card__scene {
    position: absolute;
    right: 0;
    top: 0;
    width: 400px;
    height: 380px;
  }
  .brand {
    position: absolute;
    left: 64px;
    top: 150px;
    display: flex;
    align-items: center;
    gap: 14px;
  }
  .brand__dot {
    width: 16px;
    height: 16px;
    border-radius: 50%;
    background: var(--ink);
  }
  .brand__name {
    font-family: "Cinzel", serif;
    font-weight: 400;
    font-size: 34px;
    letter-spacing: 0.5px;
    color: var(--ink);
  }
  .holder {
    position: absolute;
    left: 470px;
    top: 86px;
    font-family: "Cinzel", serif;
    font-size: 22px;
    color: var(--ink-soft);
    letter-spacing: 0.5px;
  }
  .contact {
    position: absolute;
    left: 66px;
    top: 262px;
    font-family: "Open Sans", sans-serif;
    font-size: 22px;
    line-height: 31px;
    color: var(--ink-soft);
    font-style: normal;
  }
</style>
</head>
<body>
  <main class="canvas">
    <section class="card" aria-label="Business card front">
      <svg class="card__scene" viewBox="0 0 400 380" role="img" aria-label="Faint grey silhouette of horses and a foal by a paddock fence under a large tree">
        <defs>
          <radialGradient id="sceneFade" cx="0.6" cy="0.45" r="0.6">
            <stop offset="0" stop-color="#dcdcdc"/>
            <stop offset="1" stop-color="#f8f8f8" stop-opacity="0"/>
          </radialGradient>
        </defs>
        <rect width="400" height="380" fill="url(#sceneFade)"/>
      </svg>

      <div class="brand">
        <span class="brand__dot" aria-hidden="true"></span>
        <span class="brand__name">Hacienda Monte Verda</span>
      </div>

      <p class="holder">Marta Pellingford</p>

      <address class="contact">
        Phone: 206 555 0147<br>
        7218 142nd Ave NE<br>
        Bramwell, WA 98077<br>
        HaciendaMonteVerda@brindlemail.com
      </address>
    </section>
  </main>
</body>
</html>
```